Real Estate Company Looking for Business Card Designs for 3 Executives

Hello!
Thanks so much for considering our project! We are a real estate investment company located in Edmonton, Alberta called Bellhaven Group of Companies. We invest/develop both commercial and residential real estate and are looking to create 3 DOUBLE-SIDED business cards for 3 top executives in the company! (for some reason it won't let us select the double-sided option, but yes, the cards are double sided and would be happy to tip extra)

We have certain guidelines that we want our business cards to for sure follow - the back of the Business card has to be the Black Background Version of the Logo which has already been designed and linked as a file (first file). We want the entire back of the card to simply just be the black background logo. In terms of the front of the card, would like to see a smaller version of the white background logo (linked as the second file) in the top left hand corner - of course, feel free to get creative and we can make revisions together along the way! and Then after that, just text. We want the card to be sharp, clean, easy on the eyes and highly professional looking. We would like the card to include the Full name of the Company (Bellhaven Group of Companies), Name of the Person, Title, Phone, Email. If possible please provide the front part of the card for 3 people:

1) Bellhaven Group of Companies, Liora Quenby, Chief Financial Officer, 780-555-0142, lioraquenby@bellhavengroup.example

2) Bellhaven Group of Companies, Tobias Quenby, Chief Executive Officer, 780-555-0187, tobiasquenby@bellhavengroup.example

3) Bellhaven Group of Companies, Rui Delcourt, Chief Operations Officer, 587-555-0163, ruidelcourt@bellhavengroup.example

Thank you so much for considering our project & we look forward to seeing your designs!

```html
<!DOCTYPE html>
<html lang="en">
<head>
<meta charset="utf-8">
<title>Bellhaven Group of Companies – Business Card</title>
<link href="https://fonts.googleapis.com/css2?family=Tinos:wght@700&family=Arimo:wght@400&display=swap" rel="stylesheet">
<style>
  :root {
    --backdrop: #141414;
    --card: #202020;
    --ink: #ffffff;
    --emboss: #2c2c2c;
  }
  html, body {
    margin: 0;
    padding: 0;
    width: 1200px;
    height: 1059px;
    overflow: hidden;
    background: var(--backdrop);
  }
  .canvas {
    position: relative;
    width: 1200px;
    height: 1059px;
  }
  .card {
    position: absolute;
    background: var(--card);
    box-shadow: 0 10px 24px rgba(0,0,0,0.55);
  }
  .card-front { left: 257px; top: 89px; width: 687px; height: 390px; }
  .card-back  { left: 253px; top: 547px; width: 694px; height: 393px; }

  .name-accent {
    position: absolute;
    left: 0; top: 177px;
    width: 16px; height: 38px;
    background: var(--ink);
  }
  .person-name {
    position: absolute;
    left: 27px; top: 172px;
    margin: 0;
    font-family: "Tinos", "Times New Roman", serif;
    font-weight: 700;
    font-size: 23px;
    letter-spacing: 0.3px;
    color: var(--ink);
    white-space: nowrap;
  }
  .person-title {
    position: absolute;
    left: 27px; top: 199px;
    margin: 0;
    font-family: "Arimo", Arial, sans-serif;
    font-size: 16px;
    color: var(--ink);
  }
  .company-name {
    position: absolute;
    left: 355px; top: 62px;
    width: 200px;
    margin: 0;
    font-family: "Arimo", Arial, sans-serif;
    font-weight: 400;
    font-size: 22px;
    line-height: 1.35;
    letter-spacing: 4px;
    text-transform: uppercase;
    color: var(--ink);
  }
  .contact-list {
    position: absolute;
    left: 355px; top: 274px;
    margin: 0; padding: 0;
    list-style: none;
    font-family: "Arimo", Arial, sans-serif;
    font-size: 16px;
    color: var(--ink);
  }
  .contact-list li {
    display: flex;
    align-items: center;
    height: 25.5px;
    white-space: nowrap;
  }
  .contact-icon {
    width: 13px; height: 13px;
    margin-right: 7px;
    fill: var(--ink);
    flex: none;
  }
  .back-company-name {
    position: absolute;
    left: 0; right: 0; top: 150px;
    margin: 0;
    text-align: center;
    font-family: "Arimo", Arial, sans-serif;
    font-weight: 400;
    font-size: 64px;
    letter-spacing: 10px;
    text-transform: uppercase;
    color: var(--emboss);
  }
</style>
</head>
<body>
<main class="canvas">
  <section class="card card-front">
    <div class="name-accent"></div>
    <h1 class="person-name">TOBIAS QUENBY</h1>
    <p class="person-title">Chief Executive Officer</p>

    <p class="company-name">Bellhaven Group of Companies</p>

    <ul class="contact-list">
      <li>
        <svg class="contact-icon" viewBox="0 0 24 24" aria-hidden="true"><path d="M6.6 10.8a15.1 15.1 0 0 0 6.6 6.6l2.2-2.2a1 1 0 0 1 1-.25 11.4 11.4 0 0 0 3.6.57 1 1 0 0 1 1 1V20a1 1 0 0 1-1 1A17 17 0 0 1 3 4a1 1 0 0 1 1-1h3.5a1 1 0 0 1 1 1c0 1.25.2 2.45.57 3.6a1 1 0 0 1-.25 1z"/></svg>
        780-555-0187
      </li>
      <li>
        <svg class="contact-icon" viewBox="0 0 24 24" aria-hidden="true"><path d="M2 5h20v14H2z M3 6l9 7 9-7" fill="none" stroke="#fff" stroke-width="2"/><path d="M2 5h20L12 13z"/></svg>
        tobiasquenby@bellhavengroup.example
      </li>
      <li>
        <svg class="contact-icon" viewBox="0 0 24 24" aria-hidden="true"><circle cx="12" cy="12" r="10" fill="none" stroke="#fff" stroke-width="2"/><path d="M2 12h20M12 2c3 3 3 17 0 20M12 2c-3 3-3 17 0 20" fill="none" stroke="#fff" stroke-width="1.6"/></svg>
        www.bellhavengroup.example
      </li>
    </ul>
  </section>

  <section class="card card-back">
    <p class="back-company-name">Bellhaven</p>
  </section>
</main>
</body>
</html>
```